letterhead design

We have a business card with logo, ink etc and want to develop letterhead that uses the elements of the business card logo.
Must haves...and they should be designed in, not just plopped in :)
Dr. Marlo Quint
2718 W Juniper Street
Fresno, CA 93604
559-381-7642 p
559-381-7655 f
info@brightwellchiropractic.example
www.brightwellchiropractic.example
www.facebook.example/brightwellchiro

Rather than just have the logo on the page, is there someway to silkscreen it in the background to fill the page?

Reason: I was out of town for a week.

Business

• I'd like the logo somehow silk screened in the background of the paper as well.

```html
<!DOCTYPE html>
<html lang="en">
<head>
<meta charset="utf-8">
<title>Brightwell Wellness Center – Letterhead</title>
<link href="https://fonts.googleapis.com/css2?family=Lato:wght@400;700;900&display=swap" rel="stylesheet">
<style>
  :root {
    --canvas: #efefef;
    --paper: #ffffff;
    --ink: #111111;
    --silkscreen: #e6e6e6;
    --edge: #d4d4d4;
  }
  * { margin: 0; padding: 0; box-sizing: border-box; }
  html, body {
    width: 1200px; height: 900px; overflow: hidden;
    background: var(--canvas);
    font-family: "Lato", sans-serif;
  }
  .letterhead {
    position: absolute; left: 308px; top: 37px;
    width: 582px; height: 825px;
    background: var(--paper);
    border: 1px solid var(--edge);
    overflow: hidden;
  }
  .silkscreen {
    position: absolute; left: 0; top: 0;
    width: 582px; height: 825px;
  }
  .masthead {
    position: absolute; left: 34px; top: 56px;
    display: flex; align-items: flex-start; gap: 16px;
  }
  .brand {
    width: 140px; height: 58px;
    display: flex; align-items: center; gap: 6px;
    color: var(--ink);
  }
  .brand-dot {
    width: 14px; height: 14px; border-radius: 50%;
    background: var(--ink); flex: none;
  }
  .brand-name {
    font-weight: 900; font-size: 20px; letter-spacing: 0.02em;
    line-height: 1;
  }
  .contact { color: var(--ink); font-size: 7.6px; line-height: 10.2px; padding-top: 4px; }
  .contact-name { font-weight: 700; font-size: 9px; line-height: 12px; }
</style>
</head>
<body>
  <main class="letterhead">
    <svg class="silkscreen" viewBox="0 0 582 825" aria-hidden="true">
      <circle cx="520" cy="560" r="290" fill="var(--silkscreen)"/>
      <text x="10" y="740" font-family="Lato, sans-serif" font-weight="900" font-size="150" fill="#f4f4f4">Brightwell</text>
    </svg>

    <header class="masthead">
      <div class="brand">
        <span class="brand-dot"></span>
        <span class="brand-name">Brightwell</span>
      </div>
      <address class="contact" style="font-style: normal;">
        <div class="contact-name">Dr. Marlo Quint</div>
        <div>Address: 2718 W Juniper Street, Fresno, CA 93604</div>
        <div>Phone: 559-381-7642 // Fax: 559-381-7655 // Email: info@brightwellchiropractic.example</div>
        <div>www.brightwellchiropractic.example // www.facebook.example/brightwellchiro</div>
      </address>
    </header>
  </main>
</body>
</html>
```